Business card for a Exhibition booth fabrication company

Hi. My company would like to change our corporate name card. We are an events and Exhibition stand builder company. We would like our corporate name card to resonate what we do. I need someone to create something unique that relates to the industry that I am in. The graphic designer should be creative to incorporate the elements of my industry and try to blend in well in the design of the card. Our aim is to ensure that we are unique and our card can look different from our competitors.
Updates

Target Market(s)

Marketing and events manager from all companies

Contact Information for Business Card

The business card should have the following details:
Name
Job Title
Email
Website

Colors

Designer to choose colors to be used in the design.

Requirements
Must have
• The card must be look something that is relevant to the service that I am providing. My website is: www.velmora-buildworks.com
• You can see my website to get more information on what service that I am doing
Nice to have
• On the back of my card, I would like to have a globe image with the incorporation of my company logo. This is to indicate that my services can be done in any part of the world.

```html
<!DOCTYPE html>
<html lang="en">
<head>
<meta charset="utf-8">
<title>Velmora Buildworks – Business Card</title>
<link rel="stylesheet" href="https://fonts.googleapis.com/css2?family=Montserrat:wght@600&family=Arimo:wght@400;700&display=swap">
<style>
  :root {
    --page-bg: #e9e6e1;
    --silver-light: #f4f3f1;
    --silver-mid: #d9d8d6;
    --silver-dark: #bdbcba;
    --brand-red: #c8141a;
    --brand-red-light: #e0262c;
    --brand-red-dark: #a60d12;
    --ink: #2a2a2c;
    --band-dark: #2c2b2d;
    --band-text: #c9c3bd;
    --contact-text: #f0c9c4;
    --white: #ffffff;
  }
  html, body {
    margin: 0;
    padding: 0;
    width: 1200px;
    height: 970px;
    overflow: hidden;
    background: var(--page-bg);
  }
  .canvas {
    position: relative;
    width: 1200px;
    height: 970px;
  }
  .business-card {
    position: absolute;
    left: 80px;
    top: 190px;
    width: 1040px;
    height: 590px;
    border-radius: 24px;
    overflow: hidden;
    box-shadow: 0 10px 30px rgba(0, 0, 0, 0.18);
  }
  .card-art {
    position: absolute;
    inset: 0;
    display: block;
  }
  .brand-mark {
    position: absolute;
    left: 470px;
    top: 85px;
    width: 84px;
    height: 84px;
    border-radius: 50%;
    background: var(--brand-red);
  }
  .company-name {
    position: absolute;
    left: 0;
    right: 0;
    top: 222px;
    text-align: center;
    font-family: "Montserrat", sans-serif;
    font-weight: 600;
    font-size: 33px;
    letter-spacing: 3px;
    color: var(--ink);
  }
  .person {
    position: absolute;
    right: 550px;
    top: 410px;
    text-align: right;
    font-family: "Arimo", sans-serif;
  }
  .person-name {
    font-weight: 700;
    font-size: 34px;
    color: var(--contact-text);
    line-height: 1.1;
  }
  .person-title {
    font-size: 22px;
    color: var(--contact-text);
    margin-top: 4px;
  }
  .divider {
    position: absolute;
    left: 520px;
    top: 410px;
    width: 2px;
    height: 64px;
    background: var(--contact-text);
    opacity: 0.8;
  }
  .contact-list {
    position: absolute;
    left: 550px;
    top: 410px;
    margin: 0;
    padding: 0;
    list-style: none;
    font-family: "Arimo", sans-serif;
    font-size: 23px;
    color: var(--contact-text);
  }
  .contact-list li {
    display: flex;
    align-items: center;
    gap: 20px;
    height: 34px;
  }
  .contact-icon {
    width: 22px;
    height: 22px;
    flex: none;
  }
  .website {
    position: absolute;
    left: 0;
    right: 0;
    top: 553px;
    text-align: center;
    font-family: "Arimo", sans-serif;
    font-weight: 700;
    font-size: 21px;
    letter-spacing: 4px;
    color: var(--band-text);
  }
</style>
</head>
<body>
<main class="canvas">
  <section class="business-card" aria-label="Velmora Buildworks business card">
    <svg class="card-art" viewBox="0 0 1040 590" width="1040" height="590" aria-hidden="true">
      <defs>
        <linearGradient id="silverFace" x1="0" y1="0" x2="1" y2="0">
          <stop offset="0" stop-color="var(--silver-mid)"/>
          <stop offset="0.5" stop-color="var(--silver-light)"/>
          <stop offset="1" stop-color="var(--silver-dark)"/>
        </linearGradient>
        <linearGradient id="redFace" x1="0" y1="0" x2="1" y2="0">
          <stop offset="0" stop-color="var(--brand-red-dark)"/>
          <stop offset="0.3" stop-color="var(--brand-red-light)"/>
          <stop offset="0.7" stop-color="var(--brand-red)"/>
          <stop offset="1" stop-color="var(--brand-red-dark)"/>
        </linearGradient>
      </defs>
      <rect class="card-face" x="0" y="0" width="1040" height="590" fill="url(#silverFace)"/>
      <path class="red-wave" d="M0,192 Q520,512 1040,185 L1040,540 L0,540 Z" fill="url(#redFace)"/>
      <path class="wave-highlight" d="M0,192 Q520,512 1040,185" fill="none" stroke="var(--white)" stroke-width="4" opacity="0.7"/>
      <path class="wave-line" d="M0,196 Q520,472 1040,180" fill="none" stroke="var(--ink)" stroke-width="7"/>
      <rect class="footer-rule" x="0" y="533" width="1040" height="5" fill="var(--silver-light)"/>
      <rect class="footer-band" x="0" y="538" width="1040" height="52" fill="var(--band-dark)"/>
    </svg>

    <div class="brand-mark" aria-hidden="true"></div>
    <div class="company-name">VELMORA BUILDWORKS</div>

    <div class="person">
      <div class="person-name">Dana Whitfield</div>
      <div class="person-title">Founder</div>
    </div>
    <div class="divider" aria-hidden="true"></div>

    <ul class="contact-list">
      <li>
        <svg class="contact-icon" viewBox="0 0 22 22" aria-label="Phone">
          <rect x="5" y="1.5" width="12" height="19" rx="1.5" fill="none" stroke="currentColor" stroke-width="2"/>
          <line x1="9" y1="17" x2="13" y2="17" stroke="currentColor" stroke-width="1.5"/>
        </svg>
        <span>(555) 014-2238</span>
      </li>
      <li>
        <svg class="contact-icon" viewBox="0 0 22 22" aria-label="Email">
          <rect x="1" y="4" width="20" height="14" fill="currentColor"/>
          <path d="M1,4 L11,12 L21,4" fill="none" stroke="var(--brand-red)" stroke-width="1.8"/>
        </svg>
        <span>hello@velmora-buildworks.com</span>
      </li>
    </ul>

    <div class="website">www.VELMORA-BUILDWORKS.com</div>
  </section>
</main>
</body>
</html>
```